Vantrel System Web Page Design

This project is to design 6 pages of a web based medical system for clinics, hospitals, drugs suppliers, general items suppliers, insurance company, laboratories and patients (basically all parties which could be involved in).We want the designs of the browser, button, icon and layout are based on Zeltor, which is user friendly, looks professional, simple and neat but with powerful functions. We have uploaded few pictures of another system, please do not copy its design because this is not what we are looking for, the pictures are for you to know the elements should be included in our pages. Vantrel web-base system, design 6 pages1. Login PageShould include the following elements-company id with input field-login id with input field-password with input field2. Main Page (Navigation page)Should include the following elements-Appointment-Consultation-Patient-Drugs inventory -General supplies inventory -Laboratory-Suppliers-Insurance-Reports 3. Appointment PageShould include all the the elements in the respective pictures plus the followings-Daily View, Weekly View, Monthly View buttons4. Consultation PageShould include all the the elements in the respective picture5. Patient Page5.1 General information Should include all the the elements in the respective picture5.2 medical history/lab reportsShould include all the the elements in the respective picture plus the followings-Notify patient button-Share report button.
Updated on 28 Nov:
Please stop using Harbor Suite in your designs which is not the name of our system. We have just rename our system to Vantrel, please take note.
We need the system to look professional not playful, do not use too many colors and playful icons.

```html
<!DOCTYPE html>
<html lang="en">
<head>
<meta charset="utf-8">
<title>Vantrel – Consultation</title>
<link href="https://fonts.googleapis.com/css2?family=Roboto:wght@300;400;500;700&display=swap" rel="stylesheet">
<style>
:root{
  --blue:#1c5fac;
  --blue-dark:#17529a;
  --side-bg:#e9eaed;
  --side-text:#6b6f78;
  --line:#d9dbe0;
  --text:#2a2a2a;
  --muted:#c9ccd2;
  --scroll:#7d7f84;
  --row-alt:#ececef;
}
*{box-sizing:border-box;margin:0;padding:0}
html,body{width:1200px;height:986px;overflow:hidden;background:#fff;font-family:"Roboto",Arial,sans-serif;color:var(--text)}
.app{position:relative;width:1200px;height:986px}
.abs{position:absolute}
.header{left:0;top:0;width:1200px;height:82px;background:#fafafa;border-bottom:1px solid #c9c9c9}
.brand{left:22px;top:24px;display:flex;align-items:center;gap:10px;color:var(--blue);font-size:26px;font-weight:500}
.brand-mark{width:18px;height:18px;background:var(--blue)}
.avatar{left:957px;top:13px;width:58px;height:58px;border-radius:50%;background:linear-gradient(160deg,#c9cfd8,#7c8796);border:1px solid #bbb}
.user{left:1029px;top:32px;font-size:16px;font-weight:400;color:#222}
.user-caret{left:1146px;top:34px}
.sidebar{left:0;top:82px;width:207px;height:904px;background:var(--side-bg);border-right:1px solid #d0d2d6}
.nav{position:absolute;left:0;width:207px;display:flex;align-items:center;justify-content:space-between;padding:0 20px 0 20px;font-size:16px;font-weight:700;color:var(--side-text);border-bottom:1px solid var(--line)}
.nav svg{flex:none}
.sub{position:absolute;left:50px;font-size:15px;font-weight:400;color:#222}
.sub-active{position:absolute;left:0;top:108px;width:207px;height:37px;background:var(--blue);color:#fff;font-size:15px;padding-left:50px;line-height:37px}
.vline{left:688px;top:82px;width:1px;height:727px;background:var(--line)}
.hline{height:1px;background:var(--line)}
.panel{border:1px solid #d7d9de;border-radius:3px;background:#fff}
.rec{font-size:12px;font-weight:300;line-height:18px;color:#222}
.scroll{width:8px;border-radius:4px;background:var(--scroll)}
.btn{position:absolute;height:37px;border:1.5px solid var(--blue);border-radius:3px;background:#fff;color:var(--blue);font-size:14.5px;font-weight:300;display:flex;align-items:center;justify-content:center}
.btn.off{border-color:var(--muted);color:var(--muted)}
.btn.solid{background:var(--blue);color:#fff}
.card-head{height:31px;background:var(--blue);color:#fff;font-size:12px;font-weight:500;line-height:31px;padding-left:15px;border-radius:3px 3px 0 0}
.select{left:717px;top:381px;width:325px;height:37px;border:1px solid #d7d9de;border-radius:3px}
.drug{position:absolute;left:0;width:430px;height:47px;font-size:12px;font-weight:300}
.drug.alt{background:var(--row-alt)}
.drug .name{position:absolute;left:15px;top:7px;color:var(--blue)}
.drug .f{position:absolute;top:24px;color:#222}
</style>
</head>
<body>
<div class="app">
  <header class="abs header">
    <div class="abs brand"><span class="brand-mark"></span>Vantrel</div>
    <div class="abs avatar" role="img" aria-label="User profile photo"></div>
    <div class="abs user">Evan Marlow</div>
    <svg class="abs user-caret" width="16" height="10" viewBox="0 0 16 10"><path d="M1 1l7 7 7-7" fill="none" stroke="#1c5fac" stroke-width="2.5"/></svg>
  </header>

  <nav class="abs sidebar">
    <div class="nav" style="top:20px;height:41px">Appointments
      <svg width="18" height="16" viewBox="0 0 18 16"><rect x="1" y="2" width="16" height="13" fill="none" stroke="#1c5fac" stroke-width="1.3"/><path d="M1 6h16M5 6v9M9 6v9M13 6v9M1 10h16" stroke="#1c5fac" stroke-width="1"/></svg></div>
    <div class="nav" style="top:61px;height:47px;border-bottom:none">Consultation
      <svg width="18" height="18" viewBox="0 0 18 18"><rect x="3" y="2" width="12" height="14" fill="none" stroke="#1c5fac" stroke-width="1.3"/><path d="M6 6h6M6 9h6M6 12h4" stroke="#1c5fac" stroke-width="1.2"/></svg></div>
    <div class="sub-active">Allergy</div>
    <div class="sub" style="top:158px">Medical His.</div>
    <div class="sub" style="top:197px">Immunization</div>
    <div class="sub" style="top:235px">Glucose Data H</div>
    <div class="sub" style="top:274px">BP Data G</div>
    <div class="sub" style="top:313px">Laboratory</div>
    <div class="sub" style="top:351px">Image,Doc</div>
    <div class="sub" style="top:391px">Othhers</div>
    <div class="nav" style="top:424px;height:32px;border-top:1px solid var(--line)">Patient
      <svg width="18" height="16" viewBox="0 0 18 16"><path d="M1 3v12M1 12h16v3M4 9h13v3" fill="none" stroke="#1c5fac" stroke-width="1.3"/><circle cx="5" cy="6" r="2" fill="none" stroke="#1c5fac" stroke-width="1.2"/></svg></div>
    <div class="nav" style="top:456px;height:32px">Drugs inventory
      <svg width="18" height="16" viewBox="0 0 18 16"><rect x="2" y="6" width="14" height="9" fill="none" stroke="#1c5fac" stroke-width="1.3"/><rect x="6" y="1" width="6" height="5" fill="none" stroke="#1c5fac" stroke-width="1.2"/><path d="M9 8v5M6.5 10.5h5" stroke="#1c5fac" stroke-width="1.2"/></svg></div>
    <div class="nav" style="top:488px;height:50px;line-height:19px">General supplies<br>inventory
      <svg width="18" height="16" viewBox="0 0 18 16"><rect x="1" y="2" width="16" height="13" rx="2" fill="none" stroke="#1c5fac" stroke-width="1.3"/><path d="M1 7h16M7 10h4" stroke="#1c5fac" stroke-width="1.2"/></svg></div>
    <div class="nav" style="top:538px;height:31px">Laboratory
      <svg width="18" height="16" viewBox="0 0 18 16"><path d="M5 1v9a3 3 0 0 0 6 0V1M12 4v11M1 15h16" fill="none" stroke="#1c5fac" stroke-width="1.3"/></svg></div>
    <div class="nav" style="top:569px;height:31px">Suppliers
      <svg width="18" height="16" viewBox="0 0 18 16"><circle cx="4" cy="3" r="1.6" fill="#1c5fac"/><circle cx="9" cy="3" r="1.6" fill="#1c5fac"/><circle cx="14" cy="3" r="1.6" fill="#1c5fac"/><circle cx="9" cy="11" r="3.5" fill="none" stroke="#1c5fac" stroke-width="1.3"/></svg></div>
    <div class="nav" style="top:600px;height:32px">Insurance
      <svg width="18" height="18" viewBox="0 0 18 18"><path d="M9 1l7 3v5c0 4-3 7-7 8-4-1-7-4-7-8V4z" fill="none" stroke="#1c5fac" stroke-width="1.3"/></svg></div>
    <div class="nav" style="top:632px;height:31px">Reports
      <svg width="18" height="18" viewBox="0 0 18 18"><rect x="3" y="1" width="12" height="16" fill="none" stroke="#1c5fac" stroke-width="1.3"/><path d="M6 5h6M6 8h6M6 11h6M6 14h4" stroke="#1c5fac" stroke-width="1.1"/></svg></div>
  </nav>

  <div class="abs vline"></div>
  <div class="abs hline" style="left:208px;top:346px;width:992px"></div>
  <div class="abs hline" style="left:690px;top:454px;width:510px"></div>
  <div class="abs hline" style="left:208px;top:809px;width:992px"></div>

  <section class="abs panel" style="left:235px;top:112px;width:432px;height:153px">
    <div class="rec" style="position:absolute;left:15px;top:13px">000001<br>A000001(1) MALE (01 Jan,1988, 22Yr)<br>LAU KIN WAH<br>M: 61503827,&nbsp;&nbsp;&nbsp; T: 27419605<br>28 Jan, 2010</div>
    <div class="abs scroll" style="left:418px;top:26px;height:88px"></div>
  </section>
  <div class="btn" style="left:237px;top:281px;width:92px">Add</div>
  <div class="btn off" style="left:339px;top:281px;width:91px">Edit</div>
  <div class="btn off" style="left:440px;top:281px;width:91px">Delete</div>

  <section class="abs panel" style="left:714px;top:112px;width:457px;height:153px">
    <div class="rec" style="position:absolute;left:15px;top:13px">FLAT D, 12/F<br>HOI KING COURT<br>SEA VIEW BAY</div>
    <div class="abs scroll" style="left:442px;top:6px;height:88px"></div>
  </section>
  <div class="btn" style="left:716px;top:281px;width:92px">Add</div>
  <div class="btn off" style="left:818px;top:281px;width:92px">Edit</div>
  <div class="btn" style="left:918px;top:281px;width:92px">Delete</div>

  <section class="abs panel" style="left:235px;top:374px;width:432px;height:400px;border-color:#d7d9de">
    <div class="card-head">28 JUNE, 2010</div>
    <div class="rec" style="position:absolute;left:15px;top:47px">000001<br>A000001(1) MALE (01 Jan,1988, 22Yr)<br>LAU KIN WAH<br>M: 61503827,&nbsp;&nbsp;&nbsp; T: 27419605<br>28 Jan, 2010</div>
    <div class="abs scroll" style="left:418px;top:37px;height:88px"></div>
  </section>

  <div class="abs select">
    <svg class="abs" style="left:294px;top:14px" width="16" height="10" viewBox="0 0 16 10"><path d="M1 1l7 7 7-7" fill="none" stroke="#1c5fac" stroke-width="2.5"/></svg>
  </div>
  <div class="btn" style="left:1053px;top:381px;width:91px">View</div>

  <section class="abs panel" style="left:717px;top:494px;width:432px;height:276px">
    <div class="card-head">28 JUNE, 2010</div>
    <div class="drug" style="top:43px"><span class="name">PARACETAMOL 250MG</span><span class="f" style="left:15px">Dos: 1</span><span class="f" style="left:83px">Feq:E6-PRN</span><span class="f" style="left:173px">Day:3</span><span class="f" style="left:238px">Quantity:12.00</span></div>
    <div class="drug alt" style="top:91px"><span class="name">PARACETAMOL 250MG</span><span class="f" style="left:15px">Dos: 1</span><span class="f" style="left:83px">Feq:E6-PRN</span><span class="f" style="left:173px">Day:3</span><span class="f" style="left:238px">Quantity:12.00</span></div>
    <div class="drug" style="top:138px"><span class="name">PARACETAMOL 250MG</span><span class="f" style="left:15px">Dos: 1</span><span class="f" style="left:83px">Feq:E6-PRN</span><span class="f" style="left:173px">Day:3</span><span class="f" style="left:238px">Quantity:12.00</span></div>
    <div class="abs scroll" style="left:417px;top:46px;height:88px"></div>
  </section>

  <div class="btn solid" style="left:257px;top:851px;width:92px">Next</div>
  <div class="btn" style="left:364px;top:851px;width:110px">Appoint</div>
  <div class="btn" style="left:490px;top:851px;width:111px">Search</div>
  <div class="btn" style="left:617px;top:851px;width:110px">ReCall</div>
  <div class="btn" style="left:741px;top:851px;width:110px">Write</div>
  <div class="btn" style="left:864px;top:851px;width:91px">Bill</div>
  <div class="btn" style="left:968px;top:850px;width:110px">Decument X</div>
  <div class="btn" style="left:257px;top:901px;width:90px">Print</div>
  <div class="btn" style="left:364px;top:901px;width:110px">Main</div>
</div>
</body>
</html>
```